Fitness Centre/Personal Trainer Business Card

We need a business card design for a company based in Singapore called 'Vigor Ledger'.

We are a team of Personal Trainers and we are planning to open our new training facility.

This design will also be printed/painted on the walls in our gym.

We are a new breed of personal trainers who take fitness seriously and holistically. We do not merely train our clients to be big and muscular.

We believe in wholeness. In our opinion, fitness should include: strength, speed, flexibility, mobility, stamina & agility. These are what we train for. Of course, nutrition/diet is key.

We use fitness tools such as kettlebells, QVL, Pylometric boxes, battling ropes, clubbells, medicine balls, bulgarian bags etc - functional and non-bulky tools.

I currently have a Facebook page 'Vigor Ledger SG' which shows a logo of a kettlebell. But my business focus has since changed.

Services provided:
- Kettlebell Sport Preparation
- Calisthenics Training
- Corrective Exercises
- Sports Strength & Conditioning
- 28 days Weight Loss Program
- Myofascial Rehab Therapy
- Sports/Thai Massage

Main colors for the design should be BLACK & YELLOW. We envision a design which is able to protray the holistic view we take on fitness. Also it should somewhat appeal to the ladies and not intimidate them.

Target Market(s)

People between 18-35 years old. Students and working class alike.

Industry/Entity Type

Training

Requirements
Must have
• Name: Marcus Obadiah Lim
Fitness Coach
Corrective Exercise Specialist
M: +65 9437 2065
E: marcus@sgvigorledger-example.com

Double-sided please.
Nice to have
• "What is your vigor ledger?"

```html
<!DOCTYPE html>
<html lang="en">
<head>
<meta charset="utf-8">
<title>Vigor Ledger – Business Cards</title>
<link href="https://fonts.googleapis.com/css2?family=Open+Sans:wght@400;600;700&display=swap" rel="stylesheet">
<style>
  :root {
    --yellow: #f5d60f;
    --black: #000000;
    --white: #ffffff;
    --ink: #1a1a1a;
    --stripe-dark: #2a1a14;
    --stripe-light: #e6e6e6;
    --board-light: #d6d6d6;
    --board-dark: #8e8e8e;
  }
  * { box-sizing: border-box; margin: 0; padding: 0; }
  html, body { width: 1200px; height: 716px; overflow: hidden; }
  body {
    font-family: "Open Sans", Arial, sans-serif;
    background: radial-gradient(ellipse at 50% 50%, var(--board-light) 0%, #b9b9b9 60%, var(--board-dark) 100%);
    position: relative;
  }
  .card {
    position: absolute;
    width: 534px;
    height: 306px;
    overflow: hidden;
    box-shadow: 0 1px 3px rgba(0,0,0,.35);
  }
  .card--dark { background: var(--black); color: var(--white); }
  .card--light { background: var(--white); color: var(--ink); border: 1px solid #999; }
  .card--front-dark { left: 53px; top: 41px; }
  .card--back-dark { left: 626px; top: 39px; }
  .card--front-light { left: 53px; top: 374px; }
  .card--back-light { left: 626px; top: 387px; }

  .waves { position: absolute; left: 0; top: 0; width: 534px; height: 306px; }

  .brand {
    position: absolute;
    left: 62px;
    top: 38px;
    width: 170px;
    display: flex;
    flex-direction: column;
    align-items: center;
  }
  .brand__dot {
    width: 118px; height: 118px;
    border-radius: 50%;
    background: var(--yellow);
  }
  .brand__name {
    margin-top: 12px;
    font-size: 24px;
    font-weight: 700;
    line-height: 1;
    white-space: nowrap;
  }
  .card--dark .brand__name { color: var(--white); }
  .card--light .brand__name { color: var(--ink); }

  .contact {
    position: absolute;
    left: 278px;
    top: 93px;
    max-width: 244px;
    list-style: none;
    font-size: 12.5px;
    line-height: 24px;
  }
  .contact li { display: flex; align-items: center; gap: 6px; white-space: nowrap; }
  .contact svg { width: 11px; height: 12px; flex: none; }
  .card--dark .contact svg { fill: var(--yellow); }
  .card--light .contact svg { fill: #555; }

  .person {
    position: absolute;
    right: 15px;
    bottom: 7px;
    text-align: right;
    color: var(--ink);
  }
  .person__name { font-size: 16px; font-weight: 700; line-height: 20px; }
  .person__role { font-size: 13px; line-height: 17px; }

  .services-heading { font-weight: 700; font-size: 18px; }
  .services { list-style: none; }
  .services li::before { content: "•"; margin-right: 4px; }

  .card--back-dark .services-heading {
    position: absolute; left: 273px; top: 26px; color: var(--yellow);
  }
  .card--back-dark .services {
    position: absolute; left: 266px; top: 66px;
    color: var(--yellow); font-size: 15.5px; line-height: 26.5px;
  }
  .card--back-dark .services li::before { color: var(--white); }
  .card--back-dark .tagline {
    position: absolute; left: 140px; top: 262px;
    font-size: 16px; font-weight: 700; letter-spacing: .6px;
  }

  .card--back-light .ghost-mark {
    position: absolute; left: 180px; top: 20px;
    width: 175px; height: 175px; border-radius: 50%;
    background: var(--yellow); opacity: .12;
  }
  .card--back-light .services-heading {
    position: absolute; left: 0; right: 0; top: 68px; text-align: center; color: var(--ink);
  }
  .card--back-light .services {
    position: absolute; left: 0; right: 0; top: 106px;
    display: flex; flex-wrap: wrap; justify-content: center;
    font-size: 17px; line-height: 33px; color: var(--ink);
    padding: 0 30px; column-gap: 6px;
  }
  .card--back-light .services li { white-space: nowrap; }
  .card--back-light .tagline {
    position: absolute; left: 0; right: 0; top: 259px; text-align: center;
    font-size: 16px; font-weight: 700; letter-spacing: .6px; text-transform: uppercase; color: var(--ink);
  }
</style>
</head>
<body>

<svg width="0" height="0" style="position:absolute" aria-hidden="true">
  <defs>
    <symbol id="icon-phone" viewBox="0 0 10 12"><path d="M2 0h6a1 1 0 0 1 1 1v10a1 1 0 0 1-1 1H2a1 1 0 0 1-1-1V1a1 1 0 0 1 1-1zm0 2v6h6V2zm3 7.2a.9.9 0 1 0 0 1.8.9.9 0 0 0 0-1.8z"/></symbol>
    <symbol id="icon-mail" viewBox="0 0 12 12"><path d="M0 5l6-4 6 4v6H0zm1.2 .6L6 8.6l4.8-3L6 2.4z"/></symbol>
    <symbol id="icon-web" viewBox="0 0 12 12"><path d="M6 0a6 6 0 1 1 0 12A6 6 0 0 1 6 0zm0 1.2C5 2.3 4.6 3.8 4.5 5.4h3C7.4 3.8 7 2.3 6 1.2zM1.3 5.4h2.1c.1-1.4.4-2.7 1-3.8A4.8 4.8 0 0 0 1.3 5.4zm7.3 0h2.1a4.8 4.8 0 0 0-3.1-3.8c.6 1.1.9 2.4 1 3.8zM1.3 6.6a4.8 4.8 0 0 0 3.1 3.8c-.6-1.1-.9-2.4-1-3.8zm3.2 0c.1 1.6.5 3.1 1.5 4.2 1-1.1 1.4-2.6 1.5-4.2zm4.1 0c-.1 1.4-.4 2.7-1 3.8a4.8 4.8 0 0 0 3.1-3.8z"/></symbol>
  </defs>
</svg>

<!-- Front, dark -->
<section class="card card--dark card--front-dark">
  <svg class="waves" viewBox="0 0 534 306" aria-hidden="true">
    <path d="M0 226 C130 282 320 222 534 128 L534 156 C320 246 130 298 0 250 Z" fill="var(--yellow)"/>
    <path d="M0 262 C140 304 330 238 534 162 L534 178 C330 252 140 316 0 284 Z" fill="var(--stripe-light)"/>
    <path d="M0 296 C140 322 340 245 534 185 L534 306 L0 306 Z" fill="var(--yellow)"/>
  </svg>
  <div class="brand">
    <span class="brand__dot"></span>
    <span class="brand__name">Vigor Ledger</span>
  </div>
  <ul class="contact">
    <li><svg><use href="#icon-phone"/></svg>+65 9437 2065</li>
    <li><svg><use href="#icon-mail"/></svg>marcus@sgvigorledger-example.com</li>
    <li><svg><use href="#icon-web"/></svg>www.sgvigorledger-example.com</li>
  </ul>
  <div class="person">
    <p class="person__name">Marcus Obadiah Lim</p>
    <p class="person__role">Fitness Coach</p>
    <p class="person__role">Corrective Exercise Specialist</p>
  </div>
</section>

<!-- Back, dark -->
<section class="card card--dark card--back-dark">
  <div class="brand">
    <span class="brand__dot"></span>
    <span class="brand__name">Vigor Ledger</span>
  </div>
  <h2 class="services-heading">Services</h2>
  <ul class="services">
    <li>Sports Strength &amp; Conditioning</li>
    <li>Kettlebell Sport Preparation</li>
    <li>28 days Weight Loss Program</li>
    <li>Myofascial Rehab Therapy</li>
    <li>Calisthenics Training</li>
    <li>Corrective Exercises</li>
    <li>Sports/Thai Massage</li>
  </ul>
  <p class="tagline">What is your vigor ledger?</p>
</section>

<!-- Front, light -->
<section class="card card--light card--front-light">
  <svg class="waves" viewBox="0 0 534 306" aria-hidden="true">
    <path d="M0 226 C130 282 320 222 534 128 L534 156 C320 246 130 298 0 250 Z" fill="var(--yellow)"/>
    <path d="M0 262 C140 306 330 238 534 164 L534 178 C330 252 140 320 0 280 Z" fill="var(--stripe-dark)"/>
    <path d="M0 296 C140 322 340 245 534 185 L534 306 L0 306 Z" fill="var(--yellow)"/>
  </svg>
  <div class="brand">
    <span class="brand__dot"></span>
    <span class="brand__name">Vigor Ledger</span>
  </div>
  <ul class="contact">
    <li><svg><use href="#icon-phone"/></svg>+65 9437 2065</li>
    <li><svg><use href="#icon-mail"/></svg>marcus@sgvigorledger-example.com</li>
    <li><svg><use href="#icon-web"/></svg>www.sgvigorledger-example.com</li>
  </ul>
  <div class="person">
    <p class="person__name">Marcus Obadiah Lim</p>
    <p class="person__role">Fitness Coach</p>
    <p class="person__role">Corrective Exercise Specialist</p>
  </div>
</section>

<!-- Back, light -->
<section class="card card--light card--back-light">
  <span class="ghost-mark" aria-hidden="true"></span>
  <h2 class="services-heading">Services</h2>
  <ul class="services">
    <li>Sports Strength &amp; Conditioning</li>
    <li>Sports/Thai Massage</li>
    <li>Kettlebell Sport Preparation</li>
    <li>Corrective Exercises</li>
    <li>28 days Weight Loss Program</li>
    <li>Calisthenics Training</li>
    <li>Myofascial Rehab Therapy</li>
  </ul>
  <p class="tagline">What is your vigor ledger?</p>
</section>

</body>
</html>
```